Calderbrook Consulting Ltd Brochure

We need to design a brochure to display the services our company offers.
We provide consulting services to local governments on all aspects of the administration, governance and delivery of fire and emergency services. We have a logo that we want to use which can be viewed on our website at www.calderbrookconsulting.example. We also have printed material we can supply electronically upon request.

Target Market(s)

Local governments and their fire departments.

Industry/Entity Type

Consulting

Requirements
Must have
• Our logo as seen on our website or a black and white version we can supply.
• Address and phone number
• List of services and brief description

```html
<!DOCTYPE html>
<html lang="en">
<head>
<meta charset="utf-8">
<title>Calderbrook Consulting Ltd — Training and Consulting Service Solutions</title>
<link rel="stylesheet" href="https://fonts.googleapis.com/css2?family=Jost:wght@300;500&display=swap">
<style>
  :root {
    --page: #ffffff;
    --ink: #1a1a1a;
    --grey: #8f8e8c;
    --red: #e3202f;
    --wall: #ece9e6;
    --alarm: #d8282c;
    --white: #ffffff;
  }
  html, body {
    margin: 0;
    padding: 0;
    overflow: hidden;
    background: var(--page);
  }
  .brochure-cover {
    position: relative;
    width: 928px;
    height: 1200px;
    background: var(--page);
    overflow: hidden;
    font-family: "Jost", "Futura", sans-serif;
  }
  .block { position: absolute; }
  .edge-left-dark  { left: 0;     top: 82px;  width: 82px;  height: 680px; background: var(--ink); }
  .edge-right-grey { left: 846px; top: 82px;  width: 82px;  height: 680px; background: var(--grey); }
  .edge-left-red   { left: 0;     top: 778px; width: 82px;  height: 230px; background: var(--red); }
  .edge-right-red  { left: 846px; top: 778px; width: 82px;  height: 230px; background: var(--red); }
  .hero-image {
    left: 96px; top: 82px; width: 736px; height: 680px;
    background:
      radial-gradient(ellipse 46% 42% at 48% 50%, var(--alarm) 0%, var(--alarm) 55%, rgba(216,40,44,0) 72%),
      linear-gradient(180deg, #f1efed 0%, var(--wall) 100%);
  }
  .title-band {
    left: 96px; top: 778px; width: 736px; height: 230px;
    background: var(--grey);
  }
  .title {
    position: absolute;
    right: 34px;
    top: 62px;
    margin: 0;
    text-align: right;
    color: var(--white);
    font-weight: 300;
    font-size: 41px;
    line-height: 54px;
    letter-spacing: 0.3px;
  }
  .brand {
    position: absolute;
    left: 528px;
    top: 1060px;
    display: flex;
    align-items: center;
    gap: 12px;
  }
  .brand-mark {
    width: 22px;
    height: 22px;
    background: var(--red);
  }
  .brand-name {
    color: var(--ink);
    font-weight: 500;
    font-size: 24px;
    letter-spacing: 0.2px;
  }
</style>
</head>
<body>
  <main class="brochure-cover">
    <div class="block edge-left-dark"></div>
    <div class="block hero-image" role="img" aria-label="Photo of a finger pressing a red manual fire alarm call point on a pale wall"></div>
    <div class="block edge-right-grey"></div>

    <div class="block edge-left-red"></div>
    <section class="block title-band">
      <h1 class="title">Training and<br>Consulting Service Solutions</h1>
    </section>
    <div class="block edge-right-red"></div>

    <div class="brand">
      <span class="brand-mark"></span>
      <span class="brand-name">Calderbrook Consulting Ltd</span>
    </div>
  </main>
</body>
</html>
```